e-commerce store for sport clothing online store "baseball merchandise "web application...

I want to design a UX/UI for my web application website for the online store I will provide you with the following:
1. screen shots of the initial design for the pages>
2. the logo files.
3. The brand guideline file.

the provided files (screen shots) is guideline I want to see CREATIVITY with the UX/UI DESIGN.
PS. PLEASE FOLLOW THE BRANDGUIDE LINE CAREFULLY SPECIALLY THE TYPOGRAPHY & THE COLOR CODES.

PLEASE VISIT THIS WEBSITE brightlane.varomi-qz.com to see more for the screens.

```html
<!DOCTYPE html>
<html lang="en">
<head>
<meta charset="UTF-8">
<title>Shopping Cart</title>
<link href="https://fonts.googleapis.com/css2?family=Lato:wght@400;700;900&display=swap" rel="stylesheet">
<style>
  :root {
    --navy: #0c1e3e;
    --ink: #111111;
    --text: #1c1c1c;
    --muted-card: #bcbcbc;
    --line: #cfcfcf;
    --white: #ffffff;
    --red: #b5122f;
    --dot-gray: #9a9a9a;
  }
  * { margin: 0; padding: 0; box-sizing: border-box; }
  html, body { width: 1200px; height: 2667px; overflow: hidden; background: var(--white); }
  .screen {
    position: absolute; left: 0; top: 0;
    width: 360px; height: 800px;
    transform: scale(3.33334); transform-origin: 0 0;
    font-family: 'Lato', sans-serif; color: var(--text);
    background: var(--white);
  }
  .abs { position: absolute; }

  .app-header { left: 0; top: 0; width: 360px; height: 82px; background: var(--navy); }
  .app-header .back { left: 22px; top: 31px; }
  .app-header h1 { left: 0; width: 360px; top: 30px; text-align: center; color: var(--white); font-size: 16px; font-weight: 900; letter-spacing: .2px; }

  .select-all { top: 90px; left: 13px; width: 340px; height: 20px; }
  .radio { position: absolute; width: 19px; height: 19px; border-radius: 50%; border: 1.5px solid #333; background: var(--white); }
  .select-all .label { position: absolute; left: 30px; top: 3px; font-size: 13px; }
  .select-all .count { position: absolute; right: 0; top: 3px; font-size: 13px; font-weight: 700; }

  .cart-item { left: 7px; width: 346px; border-radius: 5px; border: 1px solid var(--line); background: var(--white); box-shadow: 0 2px 4px rgba(0,0,0,.12); }
  .cart-item.is-selected { background: var(--muted-card); border-color: #8e8e8e; }
  .cart-item .thumb { position: absolute; border-radius: 3px; box-shadow: 0 1px 5px rgba(0,0,0,.25); }
  .cart-item .title { position: absolute; left: 126px; font-size: 14px; font-weight: 900; line-height: 18px; width: 150px; color: var(--ink); }
  .cart-item .price { position: absolute; right: 12px; font-size: 14px; font-weight: 900; color: var(--navy); }
  .qty { position: absolute; left: 126px; display: flex; align-items: center; gap: 6px; }
  .qty .step { width: 16px; height: 16px; border-radius: 50%; display: flex; align-items: center; justify-content: center; }
  .qty .step.minus { border: 1.5px solid var(--ink); }
  .qty .step.plus { background: var(--navy); }
  .qty .value { width: 20px; height: 17px; border: 1px solid #888; background: var(--white); font-size: 12px; text-align: center; line-height: 15px; }
  .check { position: absolute; width: 20px; height: 20px; border-radius: 50%; background: var(--ink); display: flex; align-items: center; justify-content: center; }
  .dot { position: absolute; width: 18px; height: 18px; border-radius: 50%; background: var(--dot-gray); border: 1px solid #777; }

  .voucher-input { left: 13px; top: 561px; width: 247px; height: 34px; border: 1px solid #555; border-radius: 3px; font-size: 11px; padding: 10px 10px; color: var(--ink); }
  .apply-btn { left: 274px; top: 560px; width: 79px; height: 35px; background: var(--navy); color: var(--white); border-radius: 4px; font-size: 14px; font-weight: 900; text-align: center; line-height: 35px; }

  .summary-row { left: 20px; width: 320px; font-size: 13px; display: flex; justify-content: space-between; }
  .summary-row .amount { font-weight: 700; color: var(--navy); font-size: 12px; }

  .action-bar { left: 0; top: 728px; width: 360px; height: 72px; background: var(--white); box-shadow: 0 -6px 10px rgba(0,0,0,.06); }
  .remove-btn { left: 26px; top: 756px; display: flex; align-items: center; gap: 10px; color: var(--red); font-size: 16px; font-weight: 900; }
  .checkout-btn { left: 177px; top: 746px; width: 172px; height: 46px; background: #000; color: var(--white); border-radius: 3px; font-size: 14px; font-weight: 900; text-align: center; line-height: 46px; }
</style>
</head>
<body>
<div class="screen">

  <header class="app-header abs">
    <svg class="back abs" width="20" height="20" viewBox="0 0 20 20"><path d="M18 10H3M9 3 2 10l7 7" fill="none" stroke="#fff" stroke-width="2.4" stroke-linecap="round" stroke-linejoin="round"/></svg>
    <h1 class="abs">Shopping&nbsp; Cart</h1>
  </header>

  <div class="select-all abs">
    <span class="radio" style="left:0;top:0"></span>
    <span class="label">All</span>
    <span class="count">1 Selected</span>
  </div>

  <article class="cart-item is-selected abs" style="top:118px;height:126px;">
    <div class="thumb" role="img" aria-label="Green printed kids swim trunks" style="left:20px;top:8px;width:80px;height:98px;background:linear-gradient(160deg,#cfc6b8 0%,#3f9a72 35%,#4aa67d 70%,#c9bfb0 100%);"></div>
    <span class="check" style="left:6px;top:8px;">
      <svg width="12" height="12" viewBox="0 0 12 12"><path d="M2 6.5 5 9l5-6" fill="none" stroke="#fff" stroke-width="1.8" stroke-linecap="round" stroke-linejoin="round"/></svg>
    </span>
    <div class="title" style="top:23px;">Splashy Kids Swim Trunks</div>
    <div class="qty" style="top:77px;">
      <span class="step minus"><svg width="8" height="8" viewBox="0 0 8 8"><path d="M1 4h6" stroke="#111" stroke-width="1.6"/></svg></span>
      <span class="value">1</span>
      <span class="step plus"><svg width="8" height="8" viewBox="0 0 8 8"><path d="M1 4h6M4 1v6" stroke="#fff" stroke-width="1.6"/></svg></span>
    </div>
    <div class="price" style="top:99px;">23.000 KD</div>
  </article>

  <article class="cart-item abs" style="top:260px;height:124px;">
    <span class="dot" style="left:5px;top:4px;"></span>
    <div class="thumb" role="img" aria-label="Light grey mesh trucker cap" style="left:21px;top:20px;width:78px;height:82px;background:radial-gradient(ellipse at 50% 55%,#b9bfc6 0%,#d8dce0 45%,#ffffff 75%);"></div>
    <div class="title" style="top:22px;">Bass Trucker Cap</div>
    <div class="qty" style="top:76px;">
      <span class="step minus"><svg width="8" height="8" viewBox="0 0 8 8"><path d="M1 4h6" stroke="#111" stroke-width="1.6"/></svg></span>
      <span class="value">2</span>
      <span class="step plus"><svg width="8" height="8" viewBox="0 0 8 8"><path d="M1 4h6M4 1v6" stroke="#fff" stroke-width="1.6"/></svg></span>
    </div>
    <div class="price" style="top:97px;">13.000 KD</div>
  </article>

  <div class="voucher-input abs">Enter Voucher Code</div>
  <div class="apply-btn abs">Apply</div>

  <div class="summary-row abs" style="top:624px;"><span>Subtotal</span><span class="amount">23.000 KD</span></div>
  <div class="summary-row abs" style="top:651px;"><span>Delivery Charge</span><span class="amount">1.000 KD</span></div>
  <div class="summary-row abs" style="top:678px;"><span>Total</span><span class="amount">24.000 KD</span></div>

  <div class="action-bar abs"></div>
  <div class="remove-btn abs">
    <svg width="22" height="24" viewBox="0 0 22 24"><path d="M2 5h18M8 5V2h6v3M4 5l1.2 17h11.6L18 5M9 9v9M13 9v9" fill="none" stroke="#b5122f" stroke-width="1.8" stroke-linejoin="round"/></svg>
    <span>Remove</span>
  </div>
  <div class="checkout-btn abs">Go to Checkout</div>

</div>
</body>
</html>
```